4th Generation Family Business Needs a New Card Design!

We are a family owned 4th Generation company. We are based in the Sydney, Australia area and we are desperately in need of a more modern and classy card. We are monumental masons who design, supply & erect lasting memorials throughout cemeteries in Sydney. Our customers are normally in a period of grieving. I have attached logo files that will need to be implemented on the card. Company was established 1935. Australian Owned and Operated. Card needs to be designed to PIXO.com specification.

Target Market(s)

Our target market is based upon people that a grieving for family members that have passed away. We also deal with alot of companies that own and operate cemeteries.

Industry/Entity Type

Business

Contact Information for Business Card

Simon Harcourt, Operations Manager, 0417293086, simon@harcourtmemorials.com.au
Lewis Harcourt, Director, 0491630572, lewis@harcourtmemorials.com.au
Phone # 02 9561 3048
Website: www.harcourtmemorials.com.au
Address: Suite 17, 8 Palfrey Lane, West Carlow, Sydney NSW 2156

Font styles to use
Serif
Decorative
Script

Requirements
Must have
• Would like to see the logo nicely implemented with a modern design. Embossed lettering would be a nice additive.

```html
<!DOCTYPE html>
<html lang="en">
<head>
<meta charset="utf-8">
<title>Harcourt Memorials – Business Card</title>
<link rel="stylesheet" href="https://fonts.googleapis.com/css2?family=Cinzel:wght@400;600&family=Noto+Serif:ital@0;1&display=swap">
<style>
  :root {
    --backdrop: #e4e4e4;
    --card: #f7f7f5;
    --ink: #141414;
    --gold: #d4aa1e;
    --gold-deep: #b88f10;
    --text-muted: #2b2b2b;
    --white: #ffffff;
  }
  * { margin: 0; padding: 0; box-sizing: border-box; }
  html, body {
    width: 1200px; height: 576px; overflow: hidden;
    background: var(--backdrop);
  }
  .canvas { position: relative; width: 1200px; height: 576px; }
  .card {
    position: absolute; top: 138px;
    width: 486px; height: 293px;
    background: linear-gradient(160deg, #ffffff 0%, var(--card) 60%, #efefec 100%);
    box-shadow: 0 2px 6px rgba(0,0,0,.25);
    overflow: hidden;
  }
  .card--front { left: 80px; }
  .card--back { left: 602px; }

  .wordmark {
    font-family: "Cinzel", serif; font-weight: 400; color: var(--ink);
    text-align: center; line-height: 1;
  }
  .wordmark__primary { display: block; font-size: 34px; letter-spacing: 1px; }
  .wordmark__secondary { display: block; font-size: 15px; letter-spacing: 2px; margin-top: 6px; }

  .card--front .wordmark {
    position: absolute; left: 0; right: 0; top: 112px;
  }
  .front-band {
    position: absolute; left: 0; right: 0; bottom: 0; height: 10px;
    background: linear-gradient(90deg, var(--gold-deep), var(--gold), var(--gold-deep));
  }

  .card--back .wordmark {
    position: absolute; left: 28px; top: 116px; width: 210px;
  }
  .holder {
    position: absolute; right: 22px; top: 34px; text-align: right;
  }
  .holder__name {
    font-family: "Cinzel", serif; font-weight: 600; font-size: 19px;
    letter-spacing: 1px; color: var(--ink);
  }
  .holder__role {
    font-family: "Noto Serif", serif; font-style: italic; font-size: 11.5px;
    color: var(--text-muted); margin-top: 1px;
  }
  .address {
    position: absolute; right: 22px; top: 90px; text-align: right;
    font-family: "Noto Serif", serif; font-size: 11.5px; line-height: 19px;
    color: var(--text-muted);
  }
  .swoosh { position: absolute; left: 0; top: 0; width: 486px; height: 293px; }
  .contacts {
    position: absolute; right: 22px; top: 208px; list-style: none;
    font-family: "Noto Serif", serif; font-size: 11.5px; line-height: 16.5px;
    color: var(--white); text-align: right;
  }
  .contacts li { display: flex; justify-content: flex-end; align-items: center; gap: 6px; }
  .contacts svg { width: 9px; height: 9px; fill: var(--gold); flex: none; }
</style>
</head>
<body>
<main class="canvas">

  <section class="card card--front" aria-label="Card front">
    <div class="wordmark">
      <span class="wordmark__primary">HARCOURT</span>
      <span class="wordmark__secondary">MEMORIALS</span>
    </div>
    <div class="front-band"></div>
  </section>

  <section class="card card--back" aria-label="Card back">
    <svg class="swoosh" viewBox="0 0 486 293" aria-hidden="true">
      <defs>
        <linearGradient id="goldSweep" x1="0" x2="1" y1="0" y2="0">
          <stop offset="0" stop-color="#b88f10"/>
          <stop offset=".5" stop-color="#e2bb2c"/>
          <stop offset="1" stop-color="#c99f16"/>
        </linearGradient>
        <linearGradient id="inkSweep" x1="0" x2="1" y1="1" y2="0">
          <stop offset="0" stop-color="#0c0c0c"/>
          <stop offset=".55" stop-color="#1c1c1c"/>
          <stop offset="1" stop-color="#050505"/>
        </linearGradient>
      </defs>
      <path d="M0,232 C120,300 300,268 486,150 L486,293 L0,293 Z" fill="url(#inkSweep)"/>
      <path d="M0,218 C150,292 320,236 486,141 L486,152 C320,250 150,302 0,236 Z" fill="url(#gold-sweep)" style="fill:url(#goldSweep)"/>
      <path d="M40,240 C170,262 270,248 330,226 C260,258 160,268 40,240 Z" fill="url(#goldSweep)"/>
      <path d="M0,228 C150,298 320,248 486,147" fill="none" stroke="#ffffff" stroke-width="3"/>
    </svg>

    <div class="wordmark">
      <span class="wordmark__primary">HARCOURT</span>
      <span class="wordmark__secondary">MEMORIALS</span>
    </div>

    <div class="holder">
      <p class="holder__name">SIMON HARCOURT</p>
      <p class="holder__role">Operations Manager</p>
    </div>

    <address class="address">
      Suite 17, 8 Palfrey Lane,<br>
      West Carlow, Sydney NSW 2156
    </address>

    <ul class="contacts">
      <li>0491630572
        <svg viewBox="0 0 10 10" aria-hidden="true"><path d="M2 .5h2l1 2.5-1.3 1a6 6 0 0 0 2.3 2.3l1-1.3 2.5 1v2c0 .6-.4 1-1 1C4 9 1 6 1 1.5c0-.6.4-1 1-1z"/></svg>
      </li>
      <li>02 9561 3048
        <svg viewBox="0 0 10 10" aria-hidden="true"><path d="M1 3c0-1 1-1.8 4-1.8S9 2 9 3v1H7V3H3v1H1zM2 5h6l1 4H1z"/></svg>
      </li>
      <li>harcourtmemorials.com.au
        <svg viewBox="0 0 10 10" aria-hidden="true"><path d="M0 2h10v6H0zM.8 2.6 5 5.6l4.2-3V3L5 6 .8 3z"/></svg>
      </li>
      <li>lewis@harcourtmemorials.com.au
        <svg viewBox="0 0 10 10" aria-hidden="true"><path d="M5 0a5 5 0 1 0 0 10A5 5 0 0 0 5 0zm0 1a4 4 0 0 1 1.2.2C5.6 2 5.4 3.2 5.4 4.5h3.5A4 4 0 0 0 5 1zM1.1 5.5h3.3c0 1.2.2 2.4.7 3.4A4 4 0 0 1 1.1 5.5zm0-1H4.4c0-1.2.2-2.4.7-3.4A4 4 0 0 0 1.1 4.5zm5.3 1c0 1.2-.2 2.3-.7 3.3a4 4 0 0 0 3.2-3.3z"/></svg>
      </li>
    </ul>
  </section>

</main>
</body>
</html>
```